Brochure design for London Ice rink and Ten Pin Bowling centre

We need a design for an information leaflet incorporating our core products Ten Pin Bowling, Ice skating (figure and hockey), Karaoke and also featuring video games, food and bar. The design needs to exciting, visual and promote a fun place to be.

The main focus is Ten Pin Bowling and Ice skating.

The brochure can be A4 fold or A4 twin fold to DL we have no fixed ideas

Back page will incorporate map, address etc. as per our contact us page on the website

See our Facebook page for quality image types
See current website pages for copy text and logo. Take the copy from the website pages for each area such as Ice skating. You don't have to use the full copy maybe just sections. No prices should be shown on the leaflet.

https://www.facebook.com/harborglideandlanes
http://www.harborglideandlanes.co.uk/

Target Market(s)

young and old

Industry/Entity Type

Games

Requirements
Must have
• Great exciting images
Nice to have
• Clean and crisp ten pin bowling ball and pin images
• Clever ice skating images
• Lifestyle

```html
<!DOCTYPE html>
<html lang="en">
<head>
<meta charset="UTF-8">
<title>Harbor Glide &amp; Lanes – Brochure Inner Spread</title>
<link rel="stylesheet" href="https://fonts.googleapis.com/css2?family=Ubuntu:wght@400;700&family=Roboto:wght@400;500&display=swap">
<style>
  :root {
    --page-bg: #e6e6e6;
    --brand-blue: #1d55a3;
    --brand-blue-deep: #123f82;
    --ink-white: #ffffff;
    --ink-soft: #e4ecf8;
    --cta-red: #d3222a;
    --fold-shadow: rgba(0, 0, 0, 0.18);
  }
  * { box-sizing: border-box; margin: 0; padding: 0; }
  html, body {
    width: 1200px;
    height: 847px;
    overflow: hidden;
    background: var(--page-bg);
  }
  .spread {
    position: absolute;
    left: 60px;
    top: 90px;
    width: 1080px;
    height: 667px;
    display: flex;
    box-shadow: 0 10px 30px rgba(0, 0, 0, 0.2);
  }
  .page {
    position: relative;
    width: 540px;
    height: 667px;
    overflow: hidden;
    background: linear-gradient(160deg, var(--brand-blue) 0%, var(--brand-blue-deep) 100%);
    color: var(--ink-white);
    font-family: "Roboto", Arial, sans-serif;
  }
  .page--left::after {
    content: "";
    position: absolute;
    top: 0; right: 0;
    width: 18px; height: 100%;
    background: linear-gradient(90deg, transparent, var(--fold-shadow));
    z-index: 5;
  }
  .page--right::before {
    content: "";
    position: absolute;
    top: 0; left: 0;
    width: 14px; height: 100%;
    background: linear-gradient(270deg, transparent, var(--fold-shadow));
    z-index: 5;
  }
  .photo {
    position: absolute;
    border-radius: 50%;
    border: 6px solid var(--ink-white);
  }
  .photo--skates   { left: -70px; top: -45px; width: 300px; height: 300px;
                     background: radial-gradient(circle at 55% 45%, #f2f4f7 0%, #aeb7c2 55%, #5d6672 100%); }
  .photo--bowling  { left: 290px; top: 350px; width: 330px; height: 330px;
                     background: linear-gradient(160deg, #8b95a8 0%, #c9b9a4 45%, #6b5d52 100%); }
  .photo--karaoke  { left: 320px; top: -85px; width: 280px; height: 280px;
                     background: radial-gradient(circle at 40% 60%, #e9c9b6 0%, #6f8fc7 55%, #2a3c78 100%); }
  .photo--food     { left: 292px; top: 232px; width: 180px; height: 180px;
                     background: linear-gradient(135deg, #c9925a 0%, #e8cfa0 50%, #7a4a2a 100%); }
  .photo--kids     { left: 302px; top: 352px; width: 380px; height: 380px;
                     background: radial-gradient(circle at 45% 55%, #f4d9a0 0%, #e98a4a 45%, #d94a3a 75%, #c23a6a 100%); }

  .section { position: absolute; z-index: 2; }
  .section__title {
    font-family: "Ubuntu", Arial, sans-serif;
    font-weight: 700;
    font-size: 32px;
    letter-spacing: 1px;
    text-transform: uppercase;
    line-height: 1;
  }
  .section__tagline {
    font-family: "Ubuntu", Arial, sans-serif;
    font-weight: 400;
    font-size: 14px;
    margin: 4px 0 7px;
    white-space: nowrap;
  }
  .section__body {
    font-size: 11px;
    line-height: 1.42;
    color: var(--ink-soft);
    text-align: justify;
  }
  .section__body + .section__body { margin-top: 8px; }

  .section--skating  { left: 250px; top: 36px;  width: 265px; }
  .section--bowling  { left: 30px;  top: 362px; width: 245px; }
  .section--karaoke  { left: 32px;  top: 26px;  width: 270px; }
  .section--food     { left: 32px;  top: 262px; width: 245px; }
  .section--parties  { left: 32px;  top: 440px; width: 250px; }

  .cta {
    position: absolute;
    left: 195px;
    top: 636px;
    z-index: 3;
    padding: 3px 8px;
    border-radius: 4px;
    background: var(--cta-red);
    color: var(--ink-white);
    font-family: "Ubuntu", Arial, sans-serif;
    font-weight: 700;
    font-size: 11px;
    text-transform: uppercase;
  }
</style>
</head>
<body>
  <main class="spread">
    <section class="page page--left">
      <div class="photo photo--skates" role="img" aria-label="Close-up photo of white figure skates on the ice"></div>

      <article class="section section--skating">
        <h2 class="section__title">Ice Skating</h2>
        <p class="section__tagline">live the experience of REAL ICE</p>
        <p class="section__body">Always wanted to try Ice Skating in London but never had the chance? Are you and your friends looking for something different to do? Do you want to discover an enjoyable way of spending some quality time with the family? If so, come to Harbor where you will experience all the thrills of skating on REAL ice.</p>
        <p class="section__body">Harbor's unique ice rink has state of the art colour change lighting, special effect light shows, climate control and provides the best real ice pad for Ice Skating in London.</p>
      </article>

      <article class="section section--bowling">
        <h2 class="section__title">Bowling</h2>
        <p class="section__tagline">easy to play, even if you're a beginner!!</p>
        <p class="section__body">With 12 Lanes of full size Ten Pin Bowling together with state of the art scoring and extreme lighting you are sure to have a great time Bowling in London at Harbor.</p>
        <p class="section__body">Bowling is excellent fun whether you're a family or a group of friends looking for a fun night out. And it's easy to play, even if you're a beginner!</p>
        <p class="section__body">Lane hosts are on-hand to explain the basics and get you started plus, our state-of-the-art computerised bowling system keeps you entertained throughout play. There are some great deals on at the moment so book now...</p>
      </article>

      <div class="photo photo--bowling" role="img" aria-label="Photo of friends bowling, a man releasing the ball down the lane"></div>
      <span class="cta">Book online!</span>
    </section>

    <section class="page page--right">
      <div class="photo photo--karaoke" role="img" aria-label="Photo of a group of friends singing karaoke with microphones"></div>
      <div class="photo photo--food" role="img" aria-label="Photo of the food and bar counter"></div>
      <div class="photo photo--kids" role="img" aria-label="Photo of children at a birthday party with a cake and candles"></div>

      <article class="section section--karaoke">
        <h2 class="section__title">Karaoke</h2>
        <p class="section__tagline">live it up ... at HARBOR!!!</p>
        <p class="section__body">If you and your friends are looking for Karaoke in London then Harbor Karaoke is your ideal entertainment solution with over 5,000 songs and state of the art karaoke technology. Offering private karaoke party rooms designed to hold between 12 and 20 people, touch screen song selection, plasma screens, play list functions, pitch and speed functions, comfy seating and top notch refreshments.</p>
      </article>

      <article class="section section--food">
        <h2 class="section__title">Food &amp; Bar</h2>
        <p class="section__tagline">live the experience of REAL ICE</p>
        <p class="section__body">Always wanted to try Ice Skating in London but never had the chance? Are you and your friends looking for something different to do? Do you want to discover an enjoyable way of spending some quality time with the family? If so,</p>
      </article>

      <article class="section section--parties">
        <h2 class="section__title">Kids Parties</h2>
        <p class="section__tagline">Offer them the best party ... ever!!!</p>
        <p class="section__body">Children's birthday parties at Harbor are our speciality, and with so many activities to choose from we guarantee the kids won't get bored! We offer some exceptional value packages to suit all needs.</p>
        <p class="section__body">Choose any or all combinations of Bowling, Skating, Karaoke</p>
      </article>
    </section>
  </main>
</body>
</html>
```